Design a New Business Card for Our Company

We are looking for fresh, unique, and a modern business card that reflects our roots as digital marketing agency focused on SEM.

Industry/Entity Type

Marketing

Contact Information for Business Card

looking for very unique out of the box designs. clean and modern that compliments our logo

Requirements
Must have
• colors should match our logo
• Front should have name, address, email, and phone/fax of the person, phone/fax are the same number
• back should have our url

```html
<!DOCTYPE html>
<html lang="en">
<head>
<meta charset="utf-8">
<title>Corvane Media — Business Card</title>
<link rel="stylesheet" href="https://fonts.googleapis.com/css2?family=Open+Sans:wght@400;600;700&display=swap">
<style>
  :root {
    --backdrop: #2b2b2d;
    --card-grey: #a9a9aa;
    --card-grey-dark: #9c9c9d;
    --paper: #ffffff;
    --brand-blue: #5a95d1;
    --brand-grey: #9a9a9a;
    --text-grey: #8c8c8c;
    --line-light: rgba(255,255,255,0.85);
  }
  * { box-sizing: border-box; margin: 0; padding: 0; }
  html, body {
    width: 1200px; height: 800px; overflow: hidden;
    background: var(--backdrop);
    font-family: "Open Sans", Arial, sans-serif;
  }
  .stage { position: relative; width: 1200px; height: 800px; }
  .card {
    position: absolute;
    width: 540px; height: 309px;
    overflow: hidden;
    box-shadow: 0 10px 30px rgba(0,0,0,0.45);
  }

  /* Back side */
  .card--back {
    left: 40px; top: 246px;
    background: linear-gradient(160deg, var(--card-grey) 0%, var(--card-grey-dark) 100%);
  }
  .brand {
    position: absolute;
    display: flex; align-items: center; gap: 12px;
    white-space: nowrap;
  }
  .brand__dot { width: 30px; height: 30px; border-radius: 50%; flex: none; }
  .brand__name { font-weight: 700; font-size: 38px; letter-spacing: -1px; line-height: 1; }
  .card--back .brand { left: 150px; top: 104px; }
  .card--back .brand__dot { background: var(--brand-blue); }
  .card--back .brand__name { color: var(--paper); }
  .back__rule { position: absolute; height: 1px; background: var(--line-light); }
  .back__rule--upper { left: 300px; top: 168px; width: 220px; }
  .back__rule--lower { left: 110px; top: 274px; width: 320px; }
  .back__url {
    position: absolute; left: 0; right: 0; top: 248px;
    text-align: center; color: var(--paper);
    font-size: 13px; letter-spacing: 2px;
  }

  /* Front side */
  .card--front { left: 620px; top: 246px; background: var(--paper); }
  .card--front .brand { left: 28px; top: 98px; gap: 9px; }
  .card--front .brand__dot { width: 24px; height: 24px; background: var(--brand-grey); }
  .card--front .brand__name { color: var(--brand-blue); font-size: 25px; letter-spacing: -0.5px; }
  .front__url {
    position: absolute; left: 36px; bottom: 30px;
    font-size: 15px; letter-spacing: 1.5px; color: var(--text-grey);
  }
  .front__url b { font-weight: 400; color: var(--brand-blue); }
  .contact-panel {
    position: absolute; top: 14px; right: 14px; bottom: 54px;
    width: 238px;
    background: var(--brand-blue);
    color: var(--paper);
    padding: 22px 18px 18px 30px;
  }
  .person { position: relative; padding-left: 16px; }
  .person::before {
    content: ""; position: absolute; left: 0; top: 9px;
    border-left: 11px solid #6d6d6d;
    border-top: 7px solid transparent; border-bottom: 7px solid transparent;
  }
  .person__name { font-weight: 700; font-size: 13px; line-height: 1.3; }
  .person__title { font-size: 12px; line-height: 1.3; }
  .address { margin-top: 62px; font-size: 12px; line-height: 1.45; }
  .channels { list-style: none; margin-top: 6px; font-size: 12px; }
  .channels li { display: flex; align-items: center; gap: 7px; line-height: 1.55; }
  .channels svg { width: 13px; height: 13px; flex: none; }
</style>
</head>
<body>
<main class="stage">

  <section class="card card--back" aria-label="Business card back">
    <div class="brand">
      <span class="brand__dot"></span>
      <span class="brand__name">Corvane Media</span>
    </div>
    <div class="back__rule back__rule--upper"></div>
    <p class="back__url">www.corvanemedia.com</p>
    <div class="back__rule back__rule--lower"></div>
  </section>

  <section class="card card--front" aria-label="Business card front">
    <div class="brand">
      <span class="brand__dot"></span>
      <span class="brand__name">Corvane Media</span>
    </div>
    <p class="front__url">www.<b>corvanemedia</b>.com</p>

    <div class="contact-panel">
      <div class="person">
        <p class="person__name">Dana Whitfield</p>
        <p class="person__title">Owner</p>
      </div>
      <p class="address">Corvane Media<br>48 Harbor Lane, Suite 210,<br>Tacoma, WA 98402</p>
      <ul class="channels">
        <li>
          <svg viewBox="0 0 13 13" aria-hidden="true"><rect width="13" height="13" rx="2" fill="#e9e9e9"/><path d="M4 3.2c.5 0 .9.9 1 1.4.1.4-.6.8-.5 1.1.3.8 1 1.5 1.8 1.8.3.1.7-.6 1.1-.5.5.1 1.4.5 1.4 1 0 .7-.8 1.3-1.5 1.2C5.2 8.9 4.1 7.8 3.8 5.7 3.7 4 3.5 3.2 4 3.2z" fill="#6f6f6f"/></svg>
          253.555.0147
        </li>
        <li>
          <svg viewBox="0 0 13 13" aria-hidden="true"><rect width="13" height="13" rx="2" fill="#e9e9e9"/><rect x="4" y="2.5" width="5" height="3" fill="#6f6f6f"/><rect x="2.5" y="5.5" width="8" height="4" rx="1" fill="#6f6f6f"/><rect x="4" y="8.5" width="5" height="2" fill="#bdbdbd"/></svg>
          253.555.0147
        </li>
        <li>
          <svg viewBox="0 0 13 13" aria-hidden="true"><rect width="13" height="13" rx="2" fill="#e9e9e9"/><rect x="2.5" y="3.5" width="8" height="6" fill="#6f6f6f"/><path d="M2.5 3.5l4 3.2 4-3.2" fill="none" stroke="#e9e9e9" stroke-width="0.9"/></svg>
          hello@corvanemedia.com
        </li>
      </ul>
    </div>
  </section>

</main>
</body>
</html>
```